Vorelan.com Personal Trainer/Fitness Website

I want a website to market my personal training/Outdoor Bootcamp Class services, as well as to ditribute nutrivex. I need a logo as well I included an address for the Harbor Gales 1975 logo. I'd like Vorelan in place of Harbor Gales, and in Black and white, just different enough so I can't get sued by the PBL.
https://www.pictofind.example/imgres?imgurl=http%3A%2F%2Fwww.darnell-quibury.example%2Fwp-content%2Fuploads%2F2014%2F01%2Fgales_logo4.jpg&imgrefurl=http%3A%2F%2Fwww.darnell-quibury.example%2Fpbl-logo-redesigns-harbor-gales%2F&docid=_qkwzR7TBAgXpL&tbnid=m4tpU8KdOXjnRP%3A&w=600&h=450&client=ms-android-carrier&bih=512&biw=360&ved=0ahUKEwiRtpgyp9HMAhUTwGMKHRPMBWMQMwg6KBQwFA&iact=mrc&uact=8.
It should be about 5 pages 1. home 2. about 3. Services 4. Blog/Videos and programs 5. Contact.
http://www.dorvinfitness.example.uk/ is a website I like the style of.

Target Market(s)

Seattle area

Industry/Entity Type

Fitness

Coding

Coded - Design and coding required

Number of Pages Required

4 page

Font styles to use
Serif
Sans Serif

Requirements
Must have
• A minimal look
Nice to have
• A logo similar to the 1975 Harbor Galewinds Logo, with a Small Milo Brandt ripping his shirt open(with a picture of the logo on his shirt, picture within picture) to turn into Ironjaw in the center. Skyline is black, Background and small figure white(with black logo on shirt)

```html
<!DOCTYPE html>
<html lang="en">
<head>
<meta charset="utf-8">
<title>Vorelan – Personal Training &amp; Fitness</title>
<link href="https://fonts.googleapis.com/css2?family=Raleway:wght@300;400;500;600;700&display=swap" rel="stylesheet">
<style>
:root{
  --green:#0f6e3b;
  --green-nav:#3f8a4f;
  --ink:#1c1c1c;
  --text:#444;
  --muted:#777;
  --light:#f2f2f2;
  --band:#ececec;
  --white:#fff;
  --dark:#1e2124;
}
*{box-sizing:border-box;margin:0;padding:0}
html,body{width:1200px;height:2980px;overflow:hidden}
body{position:relative;font-family:'Raleway',sans-serif;color:var(--text);background:var(--white)}
.abs{position:absolute}
section,header,footer{position:absolute;left:0;width:1200px}

/* header + hero */
.hero{top:0;height:628px;background:linear-gradient(180deg,#f6d3a3 0%,#f1b770 35%,#d88a3c 62%,#6b4a2a 82%,#3b2c1e 100%)}
.hero-photo{position:absolute;inset:0;background:radial-gradient(ellipse 320px 260px at 640px 300px,rgba(255,240,200,.75),rgba(255,240,200,0) 70%)}
.brand{left:150px;top:30px;display:flex;align-items:center;gap:10px}
.brand-dot{width:26px;height:26px;border-radius:50%;background:var(--green)}
.brand-name{font-weight:700;font-size:20px;color:var(--ink);letter-spacing:1px}
.nav{top:54px;left:0;width:1200px}
.nav a{position:absolute;font-size:13px;font-weight:500;color:var(--ink);text-decoration:none;letter-spacing:.5px}
.nav a.active{color:var(--green-nav)}
.hero-title{top:352px;width:1200px;text-align:center;font-size:52px;font-weight:300;color:var(--white);letter-spacing:2px}
.hero-copy{top:424px;width:1200px;text-align:center;font-size:15px;line-height:28px;color:#fff6e8}
.hero-btn{left:491px;top:509px;width:218px;height:41px;border-radius:4px;background:rgba(50,38,30,.8);color:var(--white);font-size:15px;font-weight:600;letter-spacing:.5px;display:flex;align-items:center;justify-content:center}
.dot{width:12px;height:12px;border-radius:50%;background:var(--white);left:1160px}

/* partners */
.partners{top:628px;height:182px;background:var(--band)}
.partner{background:#5a5a5a}

/* services */
.services{top:810px;height:456px;background:linear-gradient(180deg,#2c3338 0%,#3d4448 45%,#2a2d2e 100%)}
.section-title{width:1200px;text-align:center;font-weight:400;letter-spacing:1px}
.services .section-title{top:62px;font-size:28px;color:var(--white)}
.service-card{top:152px;height:210px;width:292px}
.service-label{position:absolute;left:82px;top:52px;width:128px;height:110px;background:rgba(30,30,30,.72);color:var(--white);text-align:center;padding-top:16px}
.service-label h3{font-size:17px;font-weight:400;line-height:27px;letter-spacing:.5px}
.service-label span{display:block;margin:6px auto 0;width:70px;border-top:1px solid rgba(255,255,255,.5);padding-top:4px;font-size:8px;letter-spacing:1px}

/* blog */
.blog{top:1266px;height:686px;background:var(--light)}
.blog-heading{left:173px;top:76px;font-size:27px;font-weight:400;color:var(--ink)}
.blog-arrows{left:996px;top:82px}
.blog-rule{left:173px;top:127px;width:857px;height:1px;background:#cfcfcf}
.post{top:157px;width:270px}
.post-image{position:relative;height:205px;box-shadow:0 14px 14px -10px rgba(0,0,0,.35)}
.post-meta{position:absolute;left:0;top:0;width:182px;height:50px;background:rgba(40,40,40,.78);color:var(--white);padding:7px 12px}
.post-meta small{display:block;font-size:9px;opacity:.85}
.post-meta p{font-size:13px;margin-top:3px}
.post-meta b{font-weight:700}
.post-social{position:absolute;right:10px;bottom:12px;display:flex;gap:6px}
.post-social i{width:20px;height:20px;border-radius:50%;background:#111;display:block}
.post h4{margin-top:34px;font-size:14px;font-weight:700;line-height:22px;color:var(--ink)}
.post p.excerpt{margin-top:16px;font-size:10.5px;line-height:21px;color:var(--muted)}
.read-more{display:inline-block;margin-top:30px;background:#111;color:var(--white);font-size:12px;padding:5px 10px}

/* testimonials */
.testimonials{top:1952px;height:423px;background:var(--white)}
.testimonials .section-title{top:50px;font-size:27px;color:var(--ink)}
.testimonial{top:116px;width:417px;height:232px;background:var(--light);box-shadow:0 18px 18px -14px rgba(0,0,0,.35)}
.t-date{position:absolute;left:40px;top:28px;font-size:13px;font-weight:700;color:var(--ink)}
.t-band{position:absolute;left:0;right:0;bottom:0;height:63px;background:var(--green)}
.t-photo{position:absolute;left:20px;top:62px;width:137px;height:151px;border:3px solid var(--white);background:linear-gradient(160deg,#c8b8a6,#8a6f5b);z-index:1}
.t-text{position:absolute;left:173px;top:56px;width:220px;font-size:10px;line-height:16px;color:var(--muted)}
.t-quote{position:absolute;left:173px;bottom:12px;font-size:38px;font-weight:700;color:var(--white);line-height:1}
.t-name{position:absolute;left:224px;bottom:32px;font-size:13px;color:var(--white)}
.t-role{position:absolute;left:224px;bottom:14px;font-size:10px;color:#d6eadb}

/* newsletter */
.newsletter{top:2375px;height:317px;background:linear-gradient(90deg,#2a1f19 0%,#3b3530 40%,#2d2a27 65%,#1b1a19 100%)}
.newsletter .section-title{top:64px;font-size:25px;color:var(--white)}
.news-copy{top:124px;left:180px;width:840px;text-align:center;font-size:11px;line-height:22px;color:#ececec}
.news-form{left:246px;top:202px;width:708px;height:58px;background:var(--white)}
.news-form span{position:absolute;left:22px;top:21px;font-size:11px;color:#aaa}
.news-btn{position:absolute;right:6px;top:8px;width:153px;height:42px;background:#111;color:var(--white);font-size:12px;font-weight:600;display:flex;align-items:center;justify-content:center;letter-spacing:.5px}

/* footer */
.footer{top:2692px;height:288px;background:var(--white)}
.foot-brand{left:163px;top:64px;display:flex;align-items:center;gap:8px}
.foot-col{top:54px;font-size:11px;line-height:22px;color:#333;text-transform:uppercase}
.foot-social{left:900px;top:60px;display:flex;gap:14px}
.foot-social i{width:12px;height:12px;border-radius:50%;background:#333;display:block}
.foot-rule{left:0;top:226px;width:1200px;height:1px;background:#e2e2e2}
.copyright{top:254px;width:1200px;text-align:center;font-size:10px;color:#444}
</style>
</head>
<body>

<header class="hero">
  <div class="hero-photo" role="img" aria-label="Woman with arms raised facing a sunset over a grassy field"></div>
  <div class="abs brand"><span class="brand-dot"></span><span class="brand-name">VORELAN</span></div>
  <nav class="abs nav">
    <a class="active" style="left:486px">HOME</a>
    <a style="left:578px">ABOUT</a>
    <a style="left:674px">SERVICES</a>
    <a style="left:786px">BLOG</a>
    <a style="left:872px">VIDEOS</a>
    <a style="left:970px">CONTACT</a>
  </nav>
  <h1 class="abs hero-title">VORELAN</h1>
  <p class="abs hero-copy">Lorem ipsum dolor sit amet, consectetur adipiscing elit, sed do eiusmod<br>tempor incididunt ut labore et dolore</p>
  <div class="abs hero-btn">GET STARTED TODAY</div>
  <span class="abs dot" style="top:487px"></span>
  <span class="abs dot" style="top:532px"></span>
  <span class="abs dot" style="top:558px"></span>
</header>

<section class="partners" aria-label="Partners">
  <div class="abs partner" style="left:200px;top:72px;width:100px;height:50px;border-radius:3px"></div>
  <div class="abs partner" style="left:366px;top:62px;width:54px;height:54px;border-radius:50%"></div>
  <div class="abs partner" style="left:506px;top:62px;width:48px;height:48px;border-radius:6px"></div>
  <div class="abs partner" style="left:626px;top:78px;width:122px;height:36px;border-radius:3px"></div>
  <div class="abs partner" style="left:796px;top:60px;width:64px;height:72px;border-radius:4px"></div>
  <div class="abs partner" style="left:900px;top:76px;width:92px;height:38px;border-radius:3px"></div>
</section>

<section class="services">
  <h2 class="abs section-title">OUR SERVICES</h2>
  <article class="abs service-card" style="left:161px;background:linear-gradient(135deg,#d9cfc8,#8a8580)" role="img" aria-label="Trainer assisting a client with a stretch on a mat">
    <div class="service-label"><h3>PERSONAL<br>TRAINING</h3><span>READ MORE</span></div>
  </article>
  <article class="abs service-card" style="left:453px;background:linear-gradient(135deg,#4a4d4f,#2a2b2c)" role="img" aria-label="Athlete lifting weights in a gym">
    <div class="service-label"><h3>FITNESS</h3><span>READ MORE</span></div>
  </article>
  <article class="abs service-card" style="left:745px;background:linear-gradient(180deg,#b8d1e6 0%,#7fa45e 55%,#8fc04a 100%)" role="img" aria-label="Group exercising outdoors in a park">
    <div class="service-label"><h3>OUTDOOR<br>BOOTCAMP</h3><span>READ MORE</span></div>
  </article>
</section>

<section class="blog">
  <h2 class="abs blog-heading">BLOG</h2>
  <svg class="abs blog-arrows" width="40" height="20" viewBox="0 0 40 20" aria-hidden="true">
    <path d="M10 4 L4 10 L10 16" fill="none" stroke="#333" stroke-width="2"/>
    <path d="M30 4 L36 10 L30 16" fill="none" stroke="#333" stroke-width="2"/>
  </svg>
  <div class="abs blog-rule"></div>

  <article class="abs post" style="left:173px">
    <div class="post-image" style="background:linear-gradient(135deg,#4b4a66,#2c2b3a)" role="img" aria-label="People doing lunges in a fitness class">
      <div class="post-meta"><small>May 10th | 2016</small><p>Posted By <b>vorelan</b></p></div>
      <div class="post-social"><i></i><i></i><i></i></div>
    </div>
    <h4>Sed ut perspiciatis unde omnis iste natus error sit voluptatem accusantium</h4>
    <p class="excerpt">Sed ut perspiciatis unde omnis iste natus error sit voluptatem accusantium doloremque laudantium, totam rem aperiam, eaque ipsa quae ab illo inventore veritatis et quasi architecto beatae vitae dicta sunt explicabo. Nemo enim ipsam voluptatem</p>
    <span class="read-more">Read More</span>
  </article>

  <article class="abs post" style="left:465px">
    <div class="post-image" style="background:linear-gradient(135deg,#f2c67a,#a88a3c)" role="img" aria-label="Woman in a sports top resting outdoors in sunlight">
      <div class="post-meta"><small>May 10th | 2016</small><p>Posted By <b>vorelan</b></p></div>
      <div class="post-social"><i></i></div>
    </div>
    <h4>Sed ut perspiciatis unde omnis iste natus error sit voluptatem accusantium</h4>
    <p class="excerpt">Sed ut perspiciatis unde omnis iste natus error sit voluptatem accusantium doloremque laudantium, totam rem aperiam, eaque ipsa quae ab illo inventore veritatis et quasi architecto beatae vitae dicta sunt explicabo. Nemo enim ipsam voluptatem</p>
    <span class="read-more">Read More</span>
  </article>

  <article class="abs post" style="left:759px">
    <div class="post-image" style="background:linear-gradient(135deg,#c9d3dc,#6f7f8c)" role="img" aria-label="Man stretching his leg on a railing by the water">
      <div class="post-meta"><small>May 10th | 2016</small><p>Posted By <b>vorelan</b></p></div>
      <div class="post-social"><i></i><i></i></div>
    </div>
    <h4>Sed ut perspiciatis unde omnis iste natus error sit voluptatem accusantium</h4>
    <p class="excerpt">Sed ut perspiciatis unde omnis iste natus error sit voluptatem accusantium doloremque laudantium, totam rem aperiam, eaque ipsa quae ab illo inventore veritatis et quasi architecto beatae vitae dicta sunt explicabo. Nemo enim ipsam voluptatem</p>
    <span class="read-more">Read More</span>
  </article>
</section>

<section class="testimonials">
  <h2 class="abs section-title">TESTIMONIALS</h2>
  <article class="abs testimonial" style="left:173px">
    <div class="t-date">May 12th | 2016</div>
    <div class="t-band"></div>
    <div class="t-photo" role="img" aria-label="Portrait of a client"></div>
    <p class="t-text">Sed ut perspiciatis unde omnis iste natus error sit voluptatem accusantium doloremque laudantium, totam rem aperiam, eaque ipsa quae ab illo inventore veritatis et quasi architecto beatae</p>
    <span class="t-quote">&ldquo;</span>
    <span class="t-name">Reid Calloway</span>
    <span class="t-role">Fitness Trainer | Texas</span>
  </article>
  <article class="abs testimonial" style="left:610px">
    <div class="t-date">May 12th | 2016</div>
    <div class="t-band"></div>
    <div class="t-photo" style="background:linear-gradient(160deg,#7a6a60,#2f2a27)" role="img" aria-label="Portrait of a client training with weights"></div>
    <p class="t-text">Sed ut perspiciatis unde omnis iste natus error sit voluptatem accusantium doloremque laudantium, totam rem aperiam, eaque ipsa quae ab illo inventore veritatis et quasi architecto beatae</p>
    <span class="t-quote">&ldquo;</span>
    <span class="t-name">Reid Calloway</span>
    <span class="t-role">Fitness Trainer | Texas</span>
  </article>
</section>

<section class="newsletter" role="img" aria-label="Athlete holding a dumbbell in a dark gym">
  <h2 class="abs section-title">SIGN UP FOR NEWSLETTER</h2>
  <p class="abs news-copy">Sed ut perspiciatis unde omnis iste natus error sit voluptatem accusantium doloremque laudantium, totam rem aperiam, eaque ipsa quae ab illo inventore veritatis et quasi architecto beatae vitae dicta sunt explicabo. Nemo enim ipsam voluptatem</p>
  <div class="abs news-form"><span>Enter Your E-mail Address</span><div class="news-btn">SUBSCRIBE NOW</div></div>
</section>

<footer class="footer">
  <div class="abs foot-brand"><span class="brand-dot"></span><span class="brand-name" style="font-size:17px">VORELAN</span></div>
  <ul class="abs foot-col" style="left:318px;list-style:none">
    <li>Home</li><li>About</li><li>Services</li><li>Blog</li><li>Videos</li><li>Contact</li>
  </ul>
  <ul class="abs foot-col" style="left:465px;list-style:none">
    <li>Terms of Service</li><li>Privacy Policy</li><li>Help</li><li>Cookies</li>
  </ul>
  <address class="abs foot-col" style="left:608px;font-style:normal">
    Halvorsen Studio<br>Lindquist Allee 42b<br>10437 Berlin &nbsp;|&nbsp; Germany<br>Telephone: +49 30 55501234<br>E-mail: hello@vorelan.example
  </address>
  <div class="abs foot-social"><i></i><i></i><i></i></div>
  <div class="abs foot-rule"></div>
  <p class="abs copyright">&copy; 2016 COMPANY NAME | ALL RIGHTS RESERVED</p>
</footer>

</body>
</html>
```